Corvane Capital Business Cards

These are professional business cards that are for my family office.
Put fake emails and phone numbers as of now until I finalize those components. This family office controls my families investments, assets, and future. The cards should be professional.
..
.
.
.
I just uploaded another variation of a logo I would like to see as a business card to I am inbeteen which logo to use

Target Market(s)

business

Industry/Entity Type

business

Contact Information for Business Card

Professional, wealth related, finance related.

Requirements
Must have
• Logo

```html
<!DOCTYPE html>
<html lang="en">
<head>
<meta charset="utf-8">
<title>Corvane Capital Business Cards</title>
<link href="https://fonts.googleapis.com/css2?family=Cinzel:wght@500&family=Montserrat:wght@400;500;600&display=swap" rel="stylesheet">
<style>
  :root {
    --backdrop: #e7e4df;
    --card-navy: #1b2131;
    --card-navy-deep: #141a28;
    --ink-white: #ffffff;
    --ink-soft: #c9ceda;
    --ink-muted: #9aa2b4;
    --accent-blue: #3f5fa8;
  }
  * { margin: 0; padding: 0; box-sizing: border-box; }
  html, body { width: 900px; height: 1200px; overflow: hidden; }
  body {
    background: var(--backdrop);
    font-family: "Montserrat", Arial, sans-serif;
    position: relative;
  }
  .card {
    position: absolute;
    left: 75px;
    width: 750px;
    height: 420px;
    border-radius: 26px;
    background: linear-gradient(135deg, var(--card-navy) 0%, var(--card-navy-deep) 100%);
    overflow: hidden;
    box-shadow: 0 10px 28px rgba(0,0,0,0.25);
  }
  .card-front { top: 165px; }
  .card-back { top: 615px; }

  .wordmark {
    position: absolute;
    font-family: "Cinzel", Georgia, serif;
    font-weight: 500;
    color: var(--ink-white);
    letter-spacing: 1px;
    white-space: nowrap;
  }
  .card-front .wordmark { left: 42px; top: 46px; font-size: 36px; }
  .card-back .wordmark { left: 42px; top: 300px; font-size: 36px; }

  .holder {
    position: absolute;
    right: 44px;
    top: 50px;
    text-align: right;
    color: var(--ink-white);
  }
  .holder-name { font-size: 22px; font-weight: 600; }
  .holder-role { font-size: 13px; color: var(--ink-soft); margin-top: 4px; }

  .address {
    position: absolute;
    left: 42px;
    top: 194px;
    font-size: 14px;
    line-height: 20px;
    color: var(--ink-soft);
  }
  .contact-list {
    position: absolute;
    left: 42px;
    top: 262px;
    list-style: none;
    font-size: 14px;
    color: var(--ink-soft);
  }
  .contact-list li { display: flex; align-items: center; gap: 10px; height: 26px; }
  .contact-list svg { width: 13px; height: 13px; fill: var(--ink-soft); }

  .emblem-ring { position: absolute; }
  .card-front .emblem-ring { left: 465px; top: 92px; width: 240px; height: 240px; }
  .card-back .emblem-ring { left: 440px; top: 40px; width: 330px; height: 330px; }

  .web-line {
    position: absolute;
    left: 50px;
    top: 350px;
    font-size: 16px;
    font-weight: 500;
    color: var(--ink-soft);
    letter-spacing: 0.5px;
  }
</style>
</head>
<body>

  <section class="card card-front" aria-label="Business card front">
    <div class="wordmark">Corvane Capital</div>

    <div class="holder">
      <div class="holder-name">Marcus Ellery</div>
      <div class="holder-role">Owner</div>
    </div>

    <div class="address">48 Harborview Plaza<br>Lakeridge, NJ 07012 USA</div>

    <ul class="contact-list">
      <li>
        <svg viewBox="0 0 24 24" aria-hidden="true"><path d="M6.6 10.8a15.1 15.1 0 0 0 6.6 6.6l2.2-2.2a1 1 0 0 1 1-.25 11.4 11.4 0 0 0 3.6.57 1 1 0 0 1 1 1V20a1 1 0 0 1-1 1A17 17 0 0 1 3 4a1 1 0 0 1 1-1h3.5a1 1 0 0 1 1 1c0 1.25.2 2.46.57 3.6a1 1 0 0 1-.25 1z"/></svg>
        (555)214-7730
      </li>
      <li>
        <svg viewBox="0 0 24 24" aria-hidden="true"><path d="M2 5h20v14H2z M4 7v.5l8 5 8-5V7l-8 5z" fill-rule="evenodd"/></svg>
        info@corvanecapital.com
      </li>
      <li>
        <svg viewBox="0 0 24 24" aria-hidden="true"><path d="M12 2a10 10 0 1 0 0 20 10 10 0 0 0 0-20zm0 2c.9 0 2.2 2 2.7 5H9.3C9.8 6 11.1 4 12 4zM4.3 11h3.8c0 .7.1 1.4.2 2H4.3a8 8 0 0 1 0-2zm11.6 0h3.8a8 8 0 0 1 0 2h-4c.1-.6.2-1.3.2-2zm-5.8 0h3.8c0 .7 0 1.4-.1 2h-3.6c-.1-.6-.1-1.3-.1-2zm-.8 4h5.4c-.5 3-1.8 5-2.7 5s-2.2-2-2.7-5z"/></svg>
        www.corvanecapital.com
      </li>
    </ul>

    <svg class="emblem-ring" viewBox="0 0 240 240" aria-hidden="true">
      <circle cx="120" cy="120" r="114" fill="none" stroke="var(--ink-white)" stroke-width="3"/>
    </svg>
  </section>

  <section class="card card-back" aria-label="Business card back">
    <svg class="emblem-ring" viewBox="0 0 330 330" aria-hidden="true">
      <circle cx="165" cy="165" r="155" fill="none" stroke="var(--accent-blue)" stroke-width="4" opacity="0.7"/>
    </svg>
    <div class="wordmark">Corvane Capital</div>
    <div class="web-line">www.corvanecapital.com</div>
  </section>

</body>
</html>
```